Awesome photographers card for an awesome new business

Double sided business card Black background and silver logo in middle on one side. Details on otherside. please keep it simple

Industry/Entity Type

Photographer

Contact Information for Business Card

Gerald Fenwick
0452817360
GeraldFenwickPhotography47@mailbox.test
www.GeraldFenwickPhotography.test.au
Instagram _Gerald_fenwick

Requirements
Must have
• My logo in Silver
• please use instagram logo instead of "Instagram"

```html
<!DOCTYPE html>
<html lang="en">
<head>
<meta charset="utf-8">
<title>Gerald Fenwick Photography – Business Card</title>
<link rel="stylesheet" href="https://fonts.googleapis.com/css2?family=PT+Sans:wght@400;700&display=swap">
<style>
  :root {
    --page-bg: #d9d3cc;
    --card-top: #2c2828;
    --card-bottom: #141212;
    --card-sheen: #4a4544;
    --silver: #cfcac6;
    --silver-dim: #8e8884;
    --name-colour: #b9ada5;
    --text-colour: #ddd6d2;
    --rule-colour: #4d4644;
    --icon-colour: #8a827e;
  }
  * { margin: 0; padding: 0; box-sizing: border-box; }
  html, body {
    width: 1200px; height: 969px; overflow: hidden;
    background: var(--page-bg);
    font-family: "PT Sans", sans-serif;
  }
  .card {
    position: absolute; left: 165px; top: 247px;
    width: 867px; height: 492px;
    background: linear-gradient(160deg, var(--card-top) 0%, var(--card-bottom) 100%);
    overflow: hidden;
  }
  .card__swoosh { position: absolute; inset: 0; }
  .brand {
    position: absolute; left: 598px; top: 134px;
    display: flex; align-items: center; gap: 12px;
  }
  .brand__dot {
    width: 14px; height: 14px; border-radius: 50%;
    background: var(--silver);
  }
  .brand__name {
    color: var(--silver); font-weight: 400; font-size: 24px;
    letter-spacing: 3px;
  }
  .holder-name {
    position: absolute; left: 52px; top: 276px;
    color: var(--name-colour); font-weight: 700; font-size: 27px;
    text-transform: uppercase;
  }
  .divider {
    position: absolute; left: 52px; top: 322px; width: 770px; height: 1px;
    background: var(--rule-colour);
  }
  .contacts {
    position: absolute; left: 52px; top: 337px; list-style: none;
  }
  .contacts__item {
    display: flex; align-items: center; height: 28px;
    color: var(--text-colour); font-size: 20px;
  }
  .contacts__icon { width: 18px; height: 18px; margin-right: 20px; flex: none; }
  .contacts__icon * { fill: var(--icon-colour); }
</style>
</head>
<body>
  <div class="card">
    <svg class="card__swoosh" viewBox="0 0 867 492" width="867" height="492">
      <path d="M0,205 C110,90 300,18 560,0 L0,0 Z" fill="var(--card-sheen)" opacity="0.75"/>
      <path d="M0,205 C110,90 300,18 560,0" fill="none" stroke="var(--silver)" stroke-width="2"/>
      <path d="M0,232 C120,110 300,30 520,0" fill="none" stroke="var(--silver-dim)" stroke-width="1.2"/>
    </svg>

    <div class="brand">
      <span class="brand__dot"></span>
      <span class="brand__name">GERALD FENWICK</span>
    </div>

    <h1 class="holder-name">Gerald Fenwick</h1>
    <div class="divider"></div>

    <ul class="contacts">
      <li class="contacts__item">
        <svg class="contacts__icon" viewBox="0 0 18 18"><path d="M3 6c0-2 2-3 6-3s6 1 6 3v1h-3V5.5H6V7H3z"/><rect x="4" y="8" width="10" height="7" rx="1"/></svg>
        0452817360
      </li>
      <li class="contacts__item">
        <svg class="contacts__icon" viewBox="0 0 18 18"><path d="M2 4h14v10H2z M3 5l6 5 6-5" /></svg>
        GeraldFenwickPhotography47@mailbox.test
      </li>
      <li class="contacts__item">
        <svg class="contacts__icon" viewBox="0 0 18 18"><circle cx="9" cy="9" r="7"/></svg>
        www.GeraldFenwickPhotography.test.au
      </li>
      <li class="contacts__item">
        <svg class="contacts__icon" viewBox="0 0 18 18"><rect x="2" y="2" width="14" height="14" rx="2"/></svg>
        Gerald_fenwick
      </li>
    </ul>
  </div>
</body>
</html>
```